Harborline Outpost Registry needs a web design

We are launching a new website and need a web design. The website is going to list every military base and installment around the world with information on each base such as a description of the base, the history of the base, contact information at the base, address, lat/long of the base, and any other relevant information including images of the base. We need a home page with navigation menu and the design of the military base page so that every military base page is formatted the same for the referenced information. We have included an example of the content that may be found on the base page(s). We are also going to have the information available in spanish.

We also wanted to mention we will be building this website in wordpress.

We also wanted to note that in the format of each base page, we will have a frequently asked questions section with answers.

```html
<!DOCTYPE html>
<html lang="en">
<head>
<meta charset="utf-8">
<title>Harborline Outpost Registry</title>
<link href="https://fonts.googleapis.com/css2?family=Cabin:wght@500;600;700&family=Roboto:wght@400;500;700&display=swap" rel="stylesheet">
<style>
:root{
  --orange:#f15a16;
  --star:#f5a623;
  --ink:#1e1e1e;
  --text:#333333;
  --muted:#7a7a7a;
  --page:#ffffff;
  --soft:#f2f2f2;
  --dark:#1b1b1b;
  --line:#e6e6e6;
}
*{box-sizing:border-box;margin:0;padding:0}
html,body{width:1200px;height:3090px;overflow:hidden}
body{font-family:"Roboto",Arial,sans-serif;color:var(--text);background:var(--page);position:relative}
.hero{position:absolute;left:0;top:0;width:1200px;height:705px;background:radial-gradient(ellipse at 50% 30%,#c98a3c 0%,#8a5a28 45%,#3e2a18 100%)}
.brand{position:absolute;left:112px;top:18px;font-family:"Cabin",sans-serif;font-weight:600;font-size:48px;color:#fff}
.nav{position:absolute;top:36px;left:604px;display:flex;gap:38px}
.nav a{color:#fff;text-decoration:none;font-weight:700;font-size:16px}
.login{position:absolute;left:982px;top:29px;width:106px;height:35px;border:1px solid #fff;border-radius:3px;color:#fff;font-size:16px;font-weight:500;display:flex;align-items:center;justify-content:center;gap:10px}
.hero-title{position:absolute;top:390px;width:100%;text-align:center;font-family:"Cabin",sans-serif;font-weight:600;font-size:50px;color:#fff;text-shadow:0 3px 6px rgba(0,0,0,.5)}
.search{position:absolute;left:281px;top:480px;width:638px;height:48px;display:flex;background:rgba(235,235,235,.92)}
.search .q{width:380px;border-right:1px solid #999;padding-left:20px;display:flex;align-items:center;font-size:16px;color:#333}
.search .loc{flex:1;padding-left:18px;display:flex;align-items:center;gap:6px;font-size:16px;color:#222}
.search .go{width:57px;background:var(--orange);display:flex;align-items:center;justify-content:center}
.section-title{position:absolute;width:100%;text-align:center;font-family:"Cabin",sans-serif;font-weight:600;font-size:40px;color:var(--ink)}
.card{position:absolute;background:#fff;box-shadow:0 0 14px rgba(0,0,0,.08)}
.photo{position:absolute;background:linear-gradient(160deg,#8d8270,#4b4436)}
.info{position:absolute}
.info h3{font-size:16px;font-weight:500;color:var(--ink);margin-bottom:10px}
.stars{display:flex;gap:3px;margin-bottom:12px}
.row{display:flex;align-items:center;gap:9px;font-size:16px;color:var(--text);margin-bottom:14px}
.btn-outline{display:inline-block;border:1px solid var(--orange);color:var(--orange);font-weight:500;font-size:15px;padding:7px 16px;border-radius:2px;margin-top:4px}
.view-more{position:absolute;left:524px;top:2080px;width:152px;height:38px;background:var(--orange);color:#fff;font-size:17px;font-weight:500;display:flex;align-items:center;justify-content:center;gap:10px}
.reviews{position:absolute;left:0;top:2205px;width:1200px;height:457px;background:var(--soft)}
.bubble{position:absolute;top:155px;width:314px;height:147px;background:#fff;border-radius:18px;padding:40px 17px 0;font-size:14px;line-height:21.5px;color:var(--muted);text-align:justify}
.bubble:after{content:"";position:absolute;left:54px;bottom:-10px;width:20px;height:20px;background:#fff;transform:rotate(45deg)}
.quote{position:absolute;top:150px}
.reviewer{position:absolute;top:325px;display:flex;align-items:center;gap:18px}
.avatar{width:56px;height:56px;border-radius:50%;background:linear-gradient(#c9c9c9,#7d7d7d)}
.reviewer b{font-size:15px;color:var(--ink)}
.reviewer small{font-size:13px;color:#666;margin-left:8px}
.footer{position:absolute;left:0;top:2662px;width:1200px;height:428px;background:var(--dark);color:#fff}
.footer h4{position:absolute;top:72px;font-size:22px;font-weight:500}
.footer h4:after{content:"";position:absolute;left:0;top:40px;width:28px;height:2px;background:#fff}
.contact{position:absolute;left:110px;display:flex;align-items:center;gap:18px;font-size:14px;font-weight:500}
.ico{width:28px;height:28px;border-radius:50%;background:#fff;display:flex;align-items:center;justify-content:center}
.subscribe{position:absolute;left:528px;top:182px;width:298px;height:46px;border-radius:23px;background:#fff;border:2px solid #fff;display:flex;align-items:center}
.subscribe span{flex:1;padding-left:18px;font-size:13px;color:#666}
.subscribe b{background:var(--orange);height:40px;width:112px;border-radius:20px;font-size:12px;display:flex;align-items:center;justify-content:center}
.social{position:absolute;top:132px;width:34px;height:34px;border-radius:50%;background:var(--orange)}
.divider{position:absolute;left:110px;top:306px;width:978px;height:1px;background:#555}
.foot-nav{position:absolute;top:346px;width:100%;display:flex;justify-content:center;gap:40px;font-size:16px;font-weight:500}
.copy{position:absolute;top:390px;width:100%;text-align:center;font-size:14px}
</style>
</head>
<body>

<header class="hero" role="img" aria-label="Helicopter and soldiers on a dusty battlefield at sunset">
  <div class="brand">Harborline</div>
  <nav class="nav"><a>History</a><a>Facilities</a><a>Support</a><a>Services</a></nav>
  <div class="login">Login <svg width="12" height="14" viewBox="0 0 12 14"><circle cx="6" cy="4" r="3.5" fill="#fff"/><path d="M0 14c0-4 2.5-6 6-6s6 2 6 6z" fill="#fff"/></svg></div>
  <h1 class="hero-title">Harborline Outpost Registry</h1>
  <div class="search">
    <div class="q">Search</div>
    <div class="loc"><svg width="11" height="15" viewBox="0 0 10 14"><path d="M5 0a5 5 0 0 0-5 5c0 4 5 9 5 9s5-5 5-9a5 5 0 0 0-5-5zm0 7a2 2 0 1 1 0-4 2 2 0 0 1 0 4z" fill="#222"/></svg>Oregon, USA.</div>
    <div class="go"><svg width="16" height="16" viewBox="0 0 16 16"><circle cx="6.5" cy="6.5" r="4.5" stroke="#fff" stroke-width="2.4" fill="none"/><path d="M10 10l4.5 4.5" stroke="#fff" stroke-width="2.6"/></svg></div>
  </div>
</header>

<svg width="0" height="0" style="position:absolute">
  <defs>
    <symbol id="star-o" viewBox="0 0 14 14"><path d="M7 1l1.8 3.9 4.2.4-3.2 2.8 1 4.1L7 10l-3.8 2.2 1-4.1L1 5.3l4.2-.4z" fill="none" stroke="#f5a623" stroke-width="1.1"/></symbol>
    <symbol id="star-f" viewBox="0 0 14 14"><path d="M7 1l1.8 3.9 4.2.4-3.2 2.8 1 4.1L7 10l-3.8 2.2 1-4.1L1 5.3l4.2-.4z" fill="#f5a623"/></symbol>
    <symbol id="phone" viewBox="0 0 14 14"><rect width="14" height="14" rx="3" fill="#888"/><path d="M4 3.5l1.5-.5 1 2-1 .8a6 6 0 0 0 2.7 2.7l.8-1 2 1-.5 1.5C8 10.5 3.5 6 4 3.5z" fill="#fff"/></symbol>
    <symbol id="pin" viewBox="0 0 10 14"><path d="M5 0a5 5 0 0 0-5 5c0 4 5 9 5 9s5-5 5-9a5 5 0 0 0-5-5zm0 7a2 2 0 1 1 0-4 2 2 0 0 1 0 4z" fill="#888"/></symbol>
    <symbol id="clock" viewBox="0 0 14 14"><circle cx="7" cy="7" r="6" fill="none" stroke="#888" stroke-width="1.6"/><path d="M7 3.5V7h2.5" stroke="#888" stroke-width="1.6" fill="none"/></symbol>
  </defs>
</svg>

<h2 class="section-title" style="top:780px">Featured Military Bases</h2>

<!-- Wide cards -->
<article class="card" style="left:112px;top:866px;width:479px;height:220px">
  <div class="photo" role="img" aria-label="Soldier walking through a ruined town" style="left:11px;top:12px;width:199px;height:196px"></div>
  <div class="info" style="left:232px;top:12px">
    <h3>Cedar Ridge Outpost</h3>
    <div class="stars"><svg width="15" height="15"><use href="#star-o"/></svg><svg width="15" height="15"><use href="#star-o"/></svg><svg width="15" height="15"><use href="#star-o"/></svg><svg width="15" height="15"><use href="#star-o"/></svg><svg width="15" height="15"><use href="#star-o"/></svg></div>
    <div class="row"><svg width="14" height="14"><use href="#phone"/></svg>(555) 014-2290</div>
    <div class="row"><svg width="10" height="14"><use href="#pin"/></svg>Cedar Ridge, OR, United States</div>
    <div class="row"><svg width="14" height="14"><use href="#clock"/></svg>10.00Am-11,00Pm</div>
    <span class="btn-outline">View More Details</span>
  </div>
</article>
<article class="card" style="left:609px;top:867px;width:480px;height:220px">
  <div class="photo" role="img" aria-label="Soldier standing by a barbed wire fence" style="left:18px;top:12px;width:200px;height:196px;background:linear-gradient(160deg,#a9a59b,#504c44)"></div>
  <div class="info" style="left:240px;top:12px">
    <h3>Cedar Ridge Outpost</h3>
    <div class="stars"><svg width="15" height="15"><use href="#star-o"/></svg><svg width="15" height="15"><use href="#star-o"/></svg><svg width="15" height="15"><use href="#star-o"/></svg><svg width="15" height="15"><use href="#star-o"/></svg><svg width="15" height="15"><use href="#star-o"/></svg></div>
    <div class="row"><svg width="14" height="14"><use href="#phone"/></svg>(555) 014-2290</div>
    <div class="row"><svg width="10" height="14"><use href="#pin"/></svg>Cedar Ridge, OR, United States</div>
    <div class="row"><svg width="14" height="14"><use href="#clock"/></svg>10.00Am-11,00Pm</div>
    <span class="btn-outline">View More Details</span>
  </div>
</article>

<!-- Grid cards row 1 -->
<article class="card" style="left:112px;top:1130px;width:307px;height:435px">
  <div class="photo" role="img" aria-label="Soldiers outside a military hangar" style="left:10px;top:10px;width:287px;height:187px;background:linear-gradient(170deg,#b7bcbd,#4c5249)"></div>
  <div class="info" style="left:34px;top:218px">
    <h3>Cedar Ridge Outpost</h3>
    <div class="stars"><svg width="15" height="15"><use href="#star-o"/></svg><svg width="15" height="15"><use href="#star-o"/></svg><svg width="15" height="15"><use href="#star-o"/></svg><svg width="15" height="15"><use href="#star-o"/></svg><svg width="15" height="15"><use href="#star-o"/></svg></div>
    <div class="row"><svg width="14" height="14"><use href="#phone"/></svg>+1 555 010 4477</div>
    <div class="row"><svg width="10" height="14"><use href="#pin"/></svg>Cedar Ridge, OR, United States</div>
    <div class="row"><svg width="14" height="14"><use href="#clock"/></svg>10.00Am-11,00Pm</div>
    <span class="btn-outline">View More Details</span>
  </div>
</article>
<article class="card" style="left:447px;top:1130px;width:307px;height:435px">
  <div class="photo" role="img" aria-label="Troops inside a lit aircraft hangar at night" style="left:10px;top:10px;width:287px;height:187px;background:linear-gradient(170deg,#3c4450,#1b2029)"></div>
  <div class="info" style="left:34px;top:218px">
    <h3>Cedar Ridge Outpost</h3>
    <div class="stars"><svg width="15" height="15"><use href="#star-o"/></svg><svg width="15" height="15"><use href="#star-o"/></svg><svg width="15" height="15"><use href="#star-o"/></svg><svg width="15" height="15"><use href="#star-o"/></svg><svg width="15" height="15"><use href="#star-o"/></svg></div>
    <div class="row"><svg width="14" height="14"><use href="#phone"/></svg>+1 555 010 4477</div>
    <div class="row"><svg width="10" height="14"><use href="#pin"/></svg>Cedar Ridge, OR, United States</div>
    <div class="row"><svg width="14" height="14"><use href="#clock"/></svg>10.00Am-11,00Pm</div>
    <span class="btn-outline">View More Details</span>
  </div>
</article>
<article class="card" style="left:782px;top:1130px;width:307px;height:435px">
  <div class="photo" role="img" aria-label="Two soldiers beside a barbed wire fence" style="left:10px;top:10px;width:287px;height:187px;background:linear-gradient(170deg,#9aa29c,#3d4239)"></div>
  <div class="info" style="left:34px;top:218px">
    <h3>Cedar Ridge Outpost</h3>
    <div class="stars"><svg width="15" height="15"><use href="#star-o"/></svg><svg width="15" height="15"><use href="#star-o"/></svg><svg width="15" height="15"><use href="#star-o"/></svg><svg width="15" height="15"><use href="#star-o"/></svg><svg width="15" height="15"><use href="#star-o"/></svg></div>
    <div class="row"><svg width="14" height="14"><use href="#phone"/></svg>+1 555 010 4477</div>
    <div class="row"><svg width="10" height="14"><use href="#pin"/></svg>Cedar Ridge, OR, United States</div>
    <div class="row"><svg width="14" height="14"><use href="#clock"/></svg>10.00Am-11,00Pm</div>
    <span class="btn-outline">View More Details</span>
  </div>
</article>

<!-- Grid cards row 2 -->
<article class="card" style="left:112px;top:1610px;width:307px;height:435px">
  <div class="photo" role="img" aria-label="Soldiers in a red-lit corridor with fires" style="left:10px;top:10px;width:287px;height:187px;background:linear-gradient(160deg,#b1413a,#3e1a16)"></div>
  <div class="info" style="left:34px;top:218px">
    <h3>Cedar Ridge Outpost</h3>
    <div class="stars"><svg width="15" height="15"><use href="#star-o"/></svg><svg width="15" height="15"><use href="#star-o"/></svg><svg width="15" height="15"><use href="#star-o"/></svg><svg width="15" height="15"><use href="#star-o"/></svg><svg width="15" height="15"><use href="#star-o"/></svg></div>
    <div class="row"><svg width="14" height="14"><use href="#phone"/></svg>(555) 014-2290</div>
    <div class="row"><svg width="10" height="14"><use href="#pin"/></svg>Cedar Ridge, OR, United States</div>
    <div class="row"><svg width="14" height="14"><use href="#clock"/></svg>10.00Am-11,00Pm</div>
    <span class="btn-outline">View More Details</span>
  </div>
</article>
<article class="card" style="left:447px;top:1610px;width:307px;height:435px">
  <div class="photo" role="img" aria-label="Tank in a desert framed by barbed wire" style="left:10px;top:10px;width:287px;height:187px;background:linear-gradient(170deg,#c9b77c,#4a4330)"></div>
  <div class="info" style="left:34px;top:218px">
    <h3>Cedar Ridge Outpost</h3>
    <div class="stars"><svg width="15" height="15"><use href="#star-o"/></svg><svg width="15" height="15"><use href="#star-o"/></svg><svg width="15" height="15"><use href="#star-o"/></svg><svg width="15" height="15"><use href="#star-o"/></svg><svg width="15" height="15"><use href="#star-o"/></svg></div>
    <div class="row"><svg width="14" height="14"><use href="#phone"/></svg>(555) 014-2290</div>
    <div class="row"><svg width="10" height="14"><use href="#pin"/></svg>Cedar Ridge, OR, United States</div>
    <div class="row"><svg width="14" height="14"><use href="#clock"/></svg>10.00Am-11,00Pm</div>
    <span class="btn-outline">View More Details</span>
  </div>
</article>
<article class="card" style="left:782px;top:1610px;width:307px;height:435px">
  <div class="photo" role="img" aria-label="Soldier walking through rubble" style="left:10px;top:10px;width:287px;height:187px;background:linear-gradient(170deg,#8f8a80,#3f3b35)"></div>
  <div class="info" style="left:34px;top:218px">
    <h3>Cedar Ridge Outpost</h3>
    <div class="stars"><svg width="15" height="15"><use href="#star-o"/></svg><svg width="15" height="15"><use href="#star-o"/></svg><svg width="15" height="15"><use href="#star-o"/></svg><svg width="15" height="15"><use href="#star-o"/></svg><svg width="15" height="15"><use href="#star-o"/></svg></div>
    <div class="row"><svg width="14" height="14"><use href="#phone"/></svg>(555) 014-2290</div>
    <div class="row"><svg width="10" height="14"><use href="#pin"/></svg>Cedar Ridge, OR, United States</div>
    <div class="row"><svg width="14" height="14"><use href="#clock"/></svg>10.00Am-11,00Pm</div>
    <span class="btn-outline">View More Details</span>
  </div>
</article>

<div class="view-more">View More <svg width="16" height="16" viewBox="0 0 16 16"><circle cx="8" cy="8" r="7.5" fill="#fff"/><path d="M6 4.5L9.5 8 6 11.5" stroke="#f15a16" stroke-width="2.2" fill="none"/></svg></div>

<section class="reviews">
  <h2 class="section-title" style="top:52px">RECENT REVIEWS</h2>

  <svg class="quote" style="left:146px" width="26" height="22" viewBox="0 0 26 22"><path d="M0 22V12C0 5 4 1 10 0v4C7 5 5.5 7 5.5 10H11v12zm15 0V12c0-7 4-11 10-12v4c-3 1-4.5 3-4.5 6H26v12z" fill="#f15a16"/></svg>
  <div class="bubble" style="left:112px">Lorem ipsum dolor sited ameted consectetur adipiscing eiusmod tempor incididunt labore dolore magna aliqua enim ad minim veniam quis nostrud exercitation ullamco laboris.</div>
  <div class="reviewer" style="left:122px"><div class="avatar" role="img" aria-label="Reviewer portrait"></div><div><b>Daniel Morrow</b><small>05/01/2021 10:48</small><div class="stars" style="margin-top:4px"><svg width="12" height="12"><use href="#star-f"/></svg><svg width="12" height="12"><use href="#star-f"/></svg><svg width="12" height="12"><use href="#star-f"/></svg><svg width="12" height="12"><use href="#star-f"/></svg><svg width="12" height="12"><use href="#star-f"/></svg></div></div></div>

  <svg class="quote" style="left:478px" width="26" height="22" viewBox="0 0 26 22"><path d="M0 22V12C0 5 4 1 10 0v4C7 5 5.5 7 5.5 10H11v12zm15 0V12c0-7 4-11 10-12v4c-3 1-4.5 3-4.5 6H26v12z" fill="#f15a16"/></svg>
  <div class="bubble" style="left:443px">Lorem ipsum dolor sited ameted consectetur adipiscing eiusmod tempor incididunt labore dolore magna aliqua enim ad minim veniam quis nostrud exercitation ullamco laboris.</div>
  <div class="reviewer" style="left:453px"><div class="avatar" role="img" aria-label="Reviewer portrait"></div><div><b>Daniel Morrow</b><small>05/01/2021 10:48</small><div class="stars" style="margin-top:4px"><svg width="12" height="12"><use href="#star-f"/></svg><svg width="12" height="12"><use href="#star-f"/></svg><svg width="12" height="12"><use href="#star-f"/></svg><svg width="12" height="12"><use href="#star-f"/></svg><svg width="12" height="12"><use href="#star-f"/></svg></div></div></div>

  <svg class="quote" style="left:809px" width="26" height="22" viewBox="0 0 26 22"><path d="M0 22V12C0 5 4 1 10 0v4C7 5 5.5 7 5.5 10H11v12zm15 0V12c0-7 4-11 10-12v4c-3 1-4.5 3-4.5 6H26v12z" fill="#f15a16"/></svg>
  <div class="bubble" style="left:774px">Lorem ipsum dolor sited ameted consectetur adipiscing eiusmod tempor incididunt labore dolore magna aliqua enim ad minim veniam quis nostrud exercitation ullamco laboris.</div>
  <div class="reviewer" style="left:784px"><div class="avatar" role="img" aria-label="Reviewer portrait"></div><div><b>Daniel Morrow</b><small>05/01/2021 10:48</small><div class="stars" style="margin-top:4px"><svg width="12" height="12"><use href="#star-f"/></svg><svg width="12" height="12"><use href="#star-f"/></svg><svg width="12" height="12"><use href="#star-f"/></svg><svg width="12" height="12"><use href="#star-f"/></svg><svg width="12" height="12"><use href="#star-f"/></svg></div></div></div>
</section>

<footer class="footer">
  <h4 style="left:110px">Address</h4>
  <div class="contact" style="top:136px"><span class="ico"><svg width="10" height="14"><use href="#pin"/></svg></span>Cedar Ridge, OR, United States</div>
  <div class="contact" style="top:194px;font-size:19px"><span class="ico"><svg width="13" height="13" viewBox="0 0 14 14"><path d="M2 1.5l2.5-.5 1.5 3-1.5 1.2a7 7 0 0 0 4.3 4.3l1.2-1.5 3 1.5-.5 2.5C6 12.5 1.5 8 2 1.5z" fill="#f15a16"/></svg></span>(555) 014-2290</div>
  <div class="contact" style="top:250px;font-weight:400;font-size:15px"><span class="ico"><svg width="13" height="10" viewBox="0 0 13 10"><rect width="13" height="10" rx="1" fill="#f15a16"/><path d="M0 1l6.5 4.5L13 1" stroke="#fff" stroke-width="1.2" fill="none"/></svg></span>info@harborline.example</div>

  <h4 style="left:528px">Subscribe Newsletter</h4>
  <p style="position:absolute;left:528px;top:128px;width:290px;font-size:14px;line-height:20px">Lorem ipsum dolor sit amet, consectetur adipiscing elit, sed do eiusmod</p>
  <div class="subscribe"><span>✉ Email Address *</span><b>SUBSCRIBE</b></div>

  <h4 style="left:963px">Follow Us On</h4>
  <div class="social" style="left:964px"></div>
  <div class="social" style="left:1004px"></div>

  <div class="divider"></div>
  <nav class="foot-nav"><span>History</span><span>/</span><span>Facilities</span><span>/</span><span>Support</span><span>/</span><span>Services</span></nav>
  <p class="copy">© 2023 Harborline. All Rights Reserved</p>
</footer>

</body>
</html>
```